QRTV Membership Web Design Project

We need a website design for QRTV membership. We need something different from what we currently have. See what we currently have: http://www.qorvatu.org/klt4/

Make provision for where members bushiness can be advertised.
Updates

We need a box for advertising members projects/business.

Make provision for where members bushiness / products can be advertised.

Target Market(s)

For members of QRTV and Intending members. Membership is for married men only.

Requirements
Must have
• Make provision for where members bushiness can be advertised.

You are to redesign: http://www.qorvatu.org/klt4/

```html
<!DOCTYPE html>
<html lang="en">
<head>
<meta charset="utf-8">
<title>QRTV Members Portal</title>
<link href="https://fonts.googleapis.com/css2?family=Arimo:wght@400;700&family=Open+Sans:wght@400;600&family=PT+Sans:wght@400&display=swap" rel="stylesheet">
<style>
:root{
  --navy:#0b3e78;
  --header-bg:#eef3f8;
  --nav-dark:#2b2b2b;
  --nav-mid:#474747;
  --frame:#4a4a4a;
  --text:#333;
  --link-red:#c8102e;
  --green:#7fe000;
  --line:#9ec3e0;
  --footer-bg:#f1f4f7;
  --box-border:#d6d6d6;
  --ad-bg:#f6f9fc;
}
*{box-sizing:border-box;margin:0;padding:0}
html,body{width:962px;height:1200px;overflow:hidden;background:#fff}
body{position:relative;font-family:"Arimo",Arial,sans-serif;color:var(--text)}
.abs{position:absolute}
.topbar{left:0;top:0;width:962px;height:16px;background:var(--navy)}
.header{left:0;top:16px;width:962px;height:112px;background:var(--header-bg)}
.brand{left:17px;top:27px;display:flex;align-items:center;gap:10px;height:90px}
.brand-dot{width:64px;height:64px;border-radius:50%;background:var(--navy)}
.brand-name{font-weight:700;font-size:22px;line-height:26px;color:var(--navy)}
.search{left:738px;top:59px;width:213px;height:25px;background:#fff;border:1px solid #dcdcdc;border-radius:3px;box-shadow:0 3px 4px rgba(0,0,0,.08);font-size:11px;color:#9a9a9a;padding:5px 9px}
.search svg{position:absolute;right:6px;top:4px}
.nav{left:17px;top:139px;width:922px;height:38px;background:linear-gradient(var(--nav-mid),var(--nav-dark));border-radius:3px;box-shadow:0 2px 3px rgba(0,0,0,.3)}
.nav a{position:absolute;top:0;height:38px;line-height:38px;color:#e8e8e8;font-family:"Open Sans",Arial,sans-serif;font-size:13px;text-decoration:none;white-space:nowrap}
.nav .home{left:0;width:71px;background:linear-gradient(#1a5ba6,var(--navy));color:#fff;text-align:center;border-radius:3px 0 0 3px}
.nav .sep{position:absolute;top:0;width:1px;height:38px;background:#1e1e1e;border-right:1px solid #5a5a5a}
.slider{left:16px;top:191px;width:925px;height:322px;background:var(--frame);border-radius:4px}
.slide-photo{left:26px;top:201px;width:905px;height:303px;border-radius:3px;background:linear-gradient(100deg,#8a5a3a 0%,#c89a6a 30%,#d9b44a 48%,#5a7fb8 65%,#7a3040 85%,#b89070 100%)}
.caption{left:26px;top:463px;width:905px;height:41px;background:rgba(60,60,60,.55);border-radius:0 0 3px 3px}
.caption-text{left:26px;top:466px;width:905px;text-align:center;font-family:"PT Sans",Arial,sans-serif;font-size:29px;color:var(--green)}
.dots{left:822px;top:479px;display:flex;gap:8px}
.dots span{width:13px;height:13px;border-radius:50%;background:#fff}
.dots span:first-child{background:var(--green)}
.slider-shadow{left:200px;top:512px;width:580px;height:20px;border-radius:50%;background:radial-gradient(ellipse at center,rgba(0,0,0,.35),rgba(0,0,0,0) 70%)}
.card{top:579px;height:166px;background:linear-gradient(#fff,#f4f4f4);border:1px solid var(--box-border);border-radius:4px;box-shadow:0 1px 3px rgba(0,0,0,.08)}
.card-title{position:absolute;top:21px;font-size:13px;color:var(--navy);white-space:nowrap}
.card-link{position:absolute;bottom:11px;right:15px;font-size:11px;color:var(--link-red)}
.card-list{position:absolute;font-size:12.5px;line-height:17.5px;color:#444;white-space:nowrap}
.card-icon{position:absolute;border-radius:6px}
.login-head{position:absolute;left:0;top:0;width:100%;height:34px;background:linear-gradient(#fff,#eee);border-bottom:1px solid #e2e2e2;border-radius:4px 4px 0 0}
.field-label{position:absolute;right:157px;font-size:10.5px;color:#666}
.field{position:absolute;left:87px;width:122px;height:22px;background:#e9ecef;border:1px solid #b8b8b8}
.btn{position:absolute;background:var(--navy);color:#fff;font-size:12px;text-align:center;border-radius:2px}
.saving-art{left:0;top:780px;width:240px;height:245px;background:radial-gradient(circle at 45% 70%,#d8d8d8,#f4f4f4 60%,#fff)}
.saving-learn{left:164px;top:1029px;font-size:14px;color:#444}
.saving-title{left:54px;top:1049px;font-size:18.5px;color:#333}
.content-shade{left:241px;top:760px;width:310px;height:366px;background:linear-gradient(90deg,#f0f2f4,#fff)}
.para{left:278px;width:600px;font-size:12.5px;line-height:20.3px;color:var(--text)}
.more{width:92px;height:30px;line-height:30px;font-size:10.5px}
.business-ad{left:262px;top:922px;width:682px;height:178px;background:var(--ad-bg);border:1px solid var(--box-border);border-radius:4px}
.business-ad-title{left:278px;top:932px;font-size:12px;color:var(--navy);letter-spacing:.3px}
.footer{left:0;top:1126px;width:962px;height:74px;background:var(--footer-bg);border-top:2px solid var(--line)}
.footer-links{left:0;top:1149px;width:962px;text-align:center;font-size:11px;color:#333;letter-spacing:.2px;word-spacing:1px;white-space:nowrap}
.footer-links span{color:#777;margin:0 6px}
.copyright{left:0;top:1178px;width:962px;text-align:center;font-size:10.5px;color:#444}
</style>
</head>
<body>
<div class="abs topbar"></div>
<header class="abs header"></header>
<div class="abs brand">
  <div class="brand-dot"></div>
  <div class="brand-name">Qorvatu Men<br>members portal</div>
</div>
<div class="abs search">Search
  <svg width="17" height="15" viewBox="0 0 17 15"><circle cx="6.5" cy="6.5" r="4.8" fill="none" stroke="#bdbdbd" stroke-width="2"/><line x1="10" y1="10" x2="15" y2="14" stroke="#bdbdbd" stroke-width="2.5" stroke-linecap="round"/></svg>
</div>

<nav class="abs nav">
  <a class="home" href="#">Home</a>
  <a style="left:97px" href="#">About us</a>
  <div class="sep" style="left:174px"></div>
  <a style="left:191px" href="#">Membership</a>
  <div class="sep" style="left:290px"></div>
  <a style="left:299px" href="#">Member Projects</a>
  <a style="left:437px" href="#">Membership Levels</a>
  <a style="left:592px" href="#">Links</a>
  <a style="left:669px" href="#">Contact us</a>
</nav>

<div class="abs slider"></div>
<div class="abs slide-photo" role="img" aria-label="Photo of a church congregation, children raising hands and smiling adults holding red Bibles"></div>
<div class="abs caption"></div>
<div class="abs caption-text">JESUS FAMILY</div>
<div class="abs dots"><span></span><span></span><span></span></div>
<div class="abs slider-shadow"></div>

<section class="abs card" style="left:13px;width:228px">
  <div class="login-head"></div>
  <div class="card-icon" role="img" aria-label="Member avatar icon" style="left:10px;top:3px;width:26px;height:28px;background:#555;border-radius:4px"></div>
  <div class="card-title" style="left:48px;top:10px;font-size:14px">LOGIN</div>
  <div class="field-label" style="top:54px">User Name :</div>
  <div class="field" style="top:52px"></div>
  <div class="field-label" style="top:90px">Password :</div>
  <div class="field" style="top:88px"></div>
  <div class="btn" style="left:90px;top:124px;width:69px;height:24px;line-height:24px">Submit</div>
</section>

<section class="abs card" style="left:260px;width:218px">
  <div class="card-title" style="left:18px">OUR OBJECTIVES</div>
  <div class="card-icon" role="img" aria-label="Light bulb icon" style="left:20px;top:62px;width:40px;height:62px;background:linear-gradient(#f5f5f5,#cfcfcf);border-radius:20px 20px 6px 6px"></div>
  <div class="card-list" style="left:93px;top:66px;line-height:36px">Who We Are<br>What We Do</div>
  <div class="card-link">Click Here &gt;&gt;</div>
</section>

<section class="abs card" style="left:493px;width:219px">
  <div class="card-title" style="left:11px;font-size:12px">MEMBERSHIP LEVELS / BENEFITS</div>
  <div class="card-icon" role="img" aria-label="Two members icon" style="left:15px;top:66px;width:62px;height:58px;background:linear-gradient(90deg,#9bbf6a,#5a8fc8)"></div>
  <div class="card-list" style="left:100px;top:65px">Associate<br>Gold<br>Silver<br>Premium</div>
  <div class="card-link">Click Here &gt;&gt;</div>
</section>

<section class="abs card" style="left:727px;width:219px">
  <div class="card-title" style="left:24px">REGISTRATION</div>
  <div class="card-icon" role="img" aria-label="Registration form with pen icon" style="left:8px;top:64px;width:62px;height:60px;background:linear-gradient(#fff,#dcdcdc);border:1px solid #ccc"></div>
  <div class="card-list" style="left:83px;top:78px">Join the Qorvatu Men<br>Int’l Follows</div>
  <div class="card-link">Click Here &gt;&gt;</div>
</section>

<div class="abs content-shade"></div>
<div class="abs saving-art" role="img" aria-label="Hand dropping a coin into a glass piggy bank filled with coins"></div>
<div class="abs saving-learn">Learn</div>
<div class="abs saving-title">The Saving Culture</div>

<p class="abs para" style="top:786px">Qorvatu Men's International Fellowship (QRTV) was established on the 19th day of July 2008 by a group of Christian men from various Church denominations. QRTV is an interdenominational and non-denominational fellowship, born out of a great and overwhelming burden for our generation and a strong desire to see the kingdom of God come and His will be done on Earth as it is in Heaven</p>
<div class="btn more" style="left:828px;top:873px">More &gt;&gt;</div>

<section class="abs business-ad" aria-label="Members' business and products"></section>
<div class="abs business-ad-title">MEMBERS' BUSINESS / PRODUCTS</div>
<p class="abs para" style="top:960px">Qorvatu Men's International Fellowship (QRTV) was established on the 19th day of July 2008 by a group of Christian men from various Church denominations. QRTV is an interdenominational and non-denominational fellowship, born out of a great and overwhelming burden for our generation and a strong desire to see the kingdom of God come and His will be done on Earth as it is in Heaven</p>
<div class="btn more" style="left:828px;top:1057px">More &gt;&gt;</div>

<footer class="abs footer"></footer>
<div class="abs footer-links">HOME<span>|</span>ABOUT US<span>|</span>BENEFITS<span>|</span>QORVATU MEN<span>|</span>SMS<span>|</span>CONSTRUCTION COMPANY<span>|</span>MEMBERSHIP LEVELS<span>|</span>LOGIN<span>|</span>CONTACT US</div>
<div class="abs copyright">© 2012 Qorvatu Men's International Fellowship, All rights reserved.</div>
</body>
</html>
```